professional business card design for technology company

We are a small technology consulting firm, specialising in consulting based around Cloud and Managed services. Our colour scheme is yellow, blue and white, as you can see in the logos. Although we are based in melbourne australia, due to the nature of our work, our clients can be located anywhere. We are looking for a clean, professional, positive look - similar to our company logo

Target Market(s)

small business

Industry/Entity Type

Business

Contact Information for Business Card

eye catching, designed to incorporate some level of raised printing. Must contain website address, phone number, name and job title

Requirements
Must have
• Logo (attached) - use of the same colour scheme

```html
<!DOCTYPE html>
<html lang="en">
<head>
<meta charset="utf-8">
<title>Nubrio Business Card</title>
<link href="https://fonts.googleapis.com/css2?family=Raleway:wght@400;500;600;700;800&display=swap" rel="stylesheet">
<style>
  :root {
    --bg: #e9e7e3;
    --card: #f7f7f6;
    --ink: #555658;
    --ink-soft: #8a8b8d;
    --blue: #26a3dc;
    --yellow: #f2cf14;
  }
  * { box-sizing: border-box; margin: 0; padding: 0; }
  html, body { width: 1200px; height: 960px; overflow: hidden; }
  body {
    background: var(--bg);
    font-family: "Raleway", sans-serif;
    color: var(--ink);
    position: relative;
  }
  .card {
    position: absolute;
    left: 250px;
    width: 700px;
    height: 400px;
    background: var(--card);
    border-bottom: 8px solid var(--blue);
    box-shadow: 0 6px 18px rgba(0,0,0,.12);
  }
  .card--front { top: 60px; }
  .card--back { top: 500px; }

  /* front */
  .front-brand {
    position: absolute;
    left: 0; right: 0; top: 140px;
    display: flex; align-items: center; justify-content: center; gap: 22px;
  }
  .brand-dot {
    width: 58px; height: 58px; border-radius: 50%;
    background: var(--blue);
  }
  .brand-name {
    font-weight: 800;
    color: var(--ink);
    letter-spacing: -1px;
    line-height: 1;
  }
  .front-brand .brand-name { font-size: 96px; }
  .front-url {
    position: absolute; left: 0; right: 0; top: 268px;
    display: flex; align-items: center; justify-content: center; gap: 12px;
    font-size: 17px; letter-spacing: 9px; color: var(--ink);
  }
  .front-url .accent { color: var(--blue); }

  /* back */
  .back-brand {
    position: absolute; left: 50px; top: 150px;
    display: flex; align-items: center; gap: 16px;
  }
  .back-brand .brand-dot { width: 44px; height: 44px; }
  .back-brand .brand-name { font-size: 72px; }
  .contact {
    position: absolute; left: 400px; top: 92px;
    list-style: none;
  }
  .contact li { display: flex; align-items: center; gap: 14px; }
  .contact .person { margin-bottom: 34px; }
  .contact .line { margin-bottom: 14px; font-size: 16px; font-weight: 500; }
  .icon {
    width: 34px; height: 34px; border-radius: 50%;
    border: 2px solid var(--ink-soft);
    display: flex; align-items: center; justify-content: center;
    flex: none;
  }
  .icon--large { width: 42px; height: 42px; }
  .person-name { font-size: 21px; font-weight: 800; letter-spacing: .5px; text-transform: uppercase; }
  .person-name .last { color: var(--blue); font-weight: 500; }
  .person-role { font-size: 14px; color: var(--ink-soft); }
  .accent { color: var(--blue); }
</style>
</head>
<body>

<section class="card card--front">
  <div class="front-brand">
    <span class="brand-dot"></span>
    <span class="brand-name">Nubrio</span>
  </div>
  <div class="front-url">
    <svg width="14" height="14" viewBox="0 0 14 14" aria-hidden="true"><circle cx="7" cy="7" r="7" fill="var(--blue)"/><path d="M2 7h10M7 1.5c-2.4 3-2.4 8 0 11M7 1.5c2.4 3 2.4 8 0 11" stroke="#fff" stroke-width="1" fill="none"/></svg>
    <span>www.nub<span class="accent">r</span>io.com</span>
  </div>
</section>

<section class="card card--back">
  <div class="back-brand">
    <span class="brand-dot"></span>
    <span class="brand-name">Nubrio</span>
  </div>
  <ul class="contact">
    <li class="person">
      <span class="icon icon--large">
        <svg width="20" height="20" viewBox="0 0 20 20" aria-hidden="true"><circle cx="10" cy="6.5" r="4" fill="var(--blue)"/><path d="M2.5 19c0-4.5 3.4-7 7.5-7s7.5 2.5 7.5 7z" fill="var(--blue)"/></svg>
      </span>
      <div>
        <div class="person-name">Daniel <span class="last">Harper</span></div>
        <div class="person-role">Sales Director</div>
      </div>
    </li>
    <li class="line">
      <span class="icon">
        <svg width="16" height="16" viewBox="0 0 16 16" aria-hidden="true"><path d="M4 1.5l2.2 3-1.4 1.6c.9 2 2.6 3.7 4.6 4.6l1.6-1.4 3 2.2-1.3 2.5C7 14 2 9 1.5 2.8z" fill="var(--blue)"/></svg>
      </span>
      <span>555-019-2847</span>
    </li>
    <li class="line">
      <span class="icon">
        <svg width="18" height="18" viewBox="0 0 18 18" aria-hidden="true"><circle cx="9" cy="9" r="8" fill="var(--blue)"/><path d="M1.5 9h15M9 1.2c-3 3.6-3 12 0 15.6M9 1.2c3 3.6 3 12 0 15.6" stroke="#fff" stroke-width="1.1" fill="none"/></svg>
      </span>
      <span>www.nub<span class="accent">r</span>io.com</span>
    </li>
    <li class="line">
      <span class="icon">
        <svg width="18" height="14" viewBox="0 0 18 14" aria-hidden="true"><rect x="1" y="1.5" width="16" height="11" rx="1" fill="var(--blue)"/><path d="M1.5 2.5l7.5 6 7.5-6" stroke="#fff" stroke-width="1.3" fill="none"/></svg>
      </span>
      <span>hello@nubrio.com</span>
    </li>
  </ul>
</section>

</body>
</html>
```